Fun, Clean Business Card For Family Focused Travel Agency

I need a business card using specific colors and fonts as in the uploaded files. Ideally, I would like a large image of the logo on the back and all the contact info on the front. Maybe the stars/dots somewhere in a flowy form.

I do want it the contact information to be clear and easy to read. I don't want it to look too busy. Maybe even a bit minimalist.

I plan or ordering the ROUNDED CORNER business cards from Cardwell Press, so please consider that in your design.

Target Market(s)

Families with children, couples, groups of friends

Contact Information for Business Card

Marla Quint, Owner
Marla@TumbleTrips.example
Cell Phone Number 555-218-4603
Office Phone Number 555-647-1925
Specializing in Glimmerland destinations, Pelican Bay Fun Park, Cruises and All-Inclusive Vacations.

Nice but not required:
www.TumbleTrips.example
Facebook, Instagram, Twitter icons with username: TumbleTrips

Font styles to use
Sans Serif

Requirements
Must have
• Please try to use the colors from the logo as much as possible. I understand lighter shades/colors may be needed for some things.
Should not have
• NO SERIF FONTS. That is really the only thing I do not want at all

```html
<!DOCTYPE html>
<html lang="en">
<head>
<meta charset="utf-8">
<title>TumbleTrips Business Card</title>
<link rel="stylesheet" href="https://fonts.googleapis.com/css2?family=Open+Sans:wght@400;600;700&family=Pacifico&display=swap">
<style>
  :root {
    --navy: #0e1535;
    --navy-deep: #080d26;
    --teal: #14b89a;
    --white: #ffffff;
    --stage: #2a2a2c;
    --muted: #d9dcea;
  }
  * { box-sizing: border-box; margin: 0; padding: 0; }
  html, body {
    width: 1200px; height: 892px; overflow: hidden;
    background: var(--stage);
    font-family: "Open Sans", Arial, sans-serif;
  }
  .canvas { position: relative; width: 1200px; height: 892px; }
  .card {
    position: absolute; width: 560px; height: 320px;
    border-radius: 16px; overflow: hidden;
    box-shadow: 0 14px 30px rgba(0,0,0,.45);
  }
  /* Back card */
  .card-back {
    left: 70px; top: 90px;
    background: linear-gradient(160deg, #141c45 0%, var(--navy) 55%, var(--navy-deep) 100%);
    color: var(--white); text-align: center;
  }
  .social { position: absolute; top: 18px; right: 22px; display: flex; gap: 5px; }
  .social span { width: 13px; height: 13px; border-radius: 50%; background: var(--white); }
  .brand-back {
    position: absolute; left: 0; right: 0; top: 92px;
    display: flex; align-items: center; justify-content: center; gap: 10px;
    font-weight: 700; font-size: 44px; letter-spacing: .5px;
  }
  .brand-dot { width: 18px; height: 18px; border-radius: 50%; background: var(--teal); flex: none; }
  .specialty-lead {
    position: absolute; left: 0; right: 0; top: 170px;
    font-family: "Pacifico", "Open Sans", sans-serif; font-size: 20px;
  }
  .specialty {
    position: absolute; left: 0; right: 0; top: 208px;
    font-size: 14px; line-height: 1.45; color: var(--muted);
  }
  /* Front card */
  .card-front { left: 570px; top: 480px; background: var(--navy); }
  .card-front svg.shape { position: absolute; inset: 0; }
  .brand-front {
    position: absolute; left: 40px; top: 176px;
    display: flex; align-items: center; gap: 9px;
    font-weight: 700; font-size: 32px; color: var(--navy);
  }
  .person { position: absolute; right: 30px; top: 30px; text-align: right; color: var(--white); }
  .person-name { font-weight: 700; font-size: 19px; letter-spacing: .5px; }
  .person-role { font-weight: 600; font-size: 11px; letter-spacing: 1px; }
  .contacts {
    position: absolute; right: 24px; top: 158px;
    list-style: none; color: var(--white); font-size: 12px; line-height: 1.6;
  }
  .contacts li { display: flex; justify-content: flex-end; align-items: center; gap: 8px; white-space: nowrap; }
  .contacts svg { width: 12px; height: 12px; fill: var(--white); flex: none; }
</style>
</head>
<body>
<main class="canvas">

  <section class="card card-back" aria-label="Card back">
    <div class="social" aria-label="Social links"><span></span><span></span><span></span></div>
    <div class="brand-back"><span class="brand-dot"></span>TumbleTrips</div>
    <p class="specialty-lead">Specializing in</p>
    <p class="specialty">Glimmerland destinations • Pelican Bay Fun Park<br>Cruises &amp; All-Inclusive Vacations.</p>
  </section>

  <section class="card card-front" aria-label="Card front">
    <svg class="shape" viewBox="0 0 560 320" width="560" height="320" aria-hidden="true">
      <path d="M220 0 H232 C344 55 349 250 284 320 H270 C330 240 320 60 220 0 Z" fill="var(--teal)"/>
      <path d="M0 0 H220 C320 60 330 240 270 320 H0 Z" fill="var(--white)"/>
    </svg>
    <div class="brand-front"><span class="brand-dot"></span>TumbleTrips</div>
    <div class="person">
      <div class="person-name">MARLA QUINT</div>
      <div class="person-role">OWNER</div>
    </div>
    <ul class="contacts">
      <li>555-647-1925
        <svg viewBox="0 0 24 24"><path d="M6.6 10.8a15 15 0 0 0 6.6 6.6l2.2-2.2c.3-.3.7-.4 1-.2 1.1.4 2.3.6 3.6.6.6 0 1 .4 1 1V20c0 .6-.4 1-1 1A17 17 0 0 1 3 4c0-.6.4-1 1-1h3.5c.6 0 1 .4 1 1 0 1.3.2 2.5.6 3.6.1.3 0 .7-.2 1z"/></svg></li>
      <li>555-218-4603
        <svg viewBox="0 0 24 24"><path d="M7 1h10a2 2 0 0 1 2 2v18a2 2 0 0 1-2 2H7a2 2 0 0 1-2-2V3a2 2 0 0 1 2-2zm0 3v14h10V4zm5 15.5a1 1 0 1 0 0 2 1 1 0 0 0 0-2z"/></svg></li>
      <li>Marla@TumbleTrips.example
        <svg viewBox="0 0 24 24"><path d="M2 5h20v14H2zm2 2v.5l8 5 8-5V7zm0 3v7h16v-7l-8 5z"/></svg></li>
      <li>www.TumbleTrips.example
        <svg viewBox="0 0 24 24"><path d="M12 2a10 10 0 1 0 0 20 10 10 0 0 0 0-20zm-1 17.9A8 8 0 0 1 4.1 11H8c.1 3.3 1.2 6.5 3 8.9zM8 9H4.1A8 8 0 0 1 11 4.1C9.2 6.5 8.1 9 8 9zm2 2h4c-.1 2.8-.9 5.4-2 7.4-1.1-2-1.9-4.6-2-7.4zm0-2c.1-2.1.9-4.4 2-6.4 1.1 2 1.9 4.3 2 6.4zm3 10.9c1.8-2.4 2.9-5.6 3-8.9h3.9a8 8 0 0 1-6.9 8.9zM16 9c-.1 0-1.2-2.5-3-4.9A8 8 0 0 1 19.9 9z"/></svg></li>
    </ul>
  </section>

</main>
</body>
</html>
```